VFX Company Business Card Design Project

The Kestrel Works is a decentralized Visual Effects Studio servicing the television and feature film industries.
Project Brief:
Take our logo that was previously designed on Pencil Harbor and make a double sided business card.
Requirements:
- Card MUST be double sided.
- Front of card MUST have the yellow part of our logo against the dark grey background.
- Back of card is completely up to the designer.
- Back of card must include the complete company logo.
Please follow these File Preparation guidelines:
http://printnook.ca/infopage?file=filetype_en&s=PrintNook_new&lang=en
Business

```html
<!DOCTYPE html>
<html lang="en">
<head>
<meta charset="utf-8">
<title>The Kestrel Works – Business Card</title>
<link href="https://fonts.googleapis.com/css2?family=Questrial&family=Open+Sans:wght@400;600&display=swap" rel="stylesheet">
<style>
  :root {
    --backdrop: #c9a17e;
    --label: #111111;
    --card: #282828;
    --band: #5f6f6f;
    --stripe-light: #eef3e4;
    --stripe-dark: #1b1b1b;
    --text-light: #eef0ec;
    --text-soft: #d8ddd8;
    --accent: #f8c425;
  }
  * { margin: 0; padding: 0; box-sizing: border-box; }
  html, body { width: 1200px; height: 788px; overflow: hidden; }
  body {
    position: relative;
    background: var(--backdrop);
    font-family: "Questrial", "Century Gothic", sans-serif;
  }
  .view-label {
    position: absolute;
    font-family: "Open Sans", Arial, sans-serif;
    font-size: 21px;
    color: var(--label);
    transform: translateX(-50%);
    white-space: nowrap;
  }
  .label-back { left: 600px; top: 32px; }
  .label-front-1 { left: 327px; top: 403px; }
  .label-front-2 { left: 900px; top: 403px; }

  .card {
    position: absolute;
    width: 525px;
    height: 300px;
    border-radius: 22px;
    background: var(--card);
    overflow: hidden;
    box-shadow: 0 3px 8px rgba(0,0,0,0.35);
  }
  .card-back { left: 338px; top: 78px; }
  .card-front-1 { left: 54px; top: 445px; }
  .card-front-2 { left: 622px; top: 445px; }

  .wave { position: absolute; left: 0; top: 0; width: 525px; height: 300px; }

  .holder { position: absolute; right: 27px; top: 28px; text-align: right; }
  .holder-name { font-size: 19px; color: var(--text-light); letter-spacing: 0.5px; }
  .holder-role { font-size: 13px; color: var(--text-soft); letter-spacing: 1px; margin-top: 1px; }

  .brand-name {
    position: absolute;
    left: 28px;
    top: 128px;
    font-size: 33px;
    color: var(--text-light);
    letter-spacing: 0.5px;
  }

  .address {
    position: absolute;
    left: 27px;
    top: 249px;
    font-family: "Open Sans", Arial, sans-serif;
    font-size: 12.5px;
    line-height: 16px;
    color: var(--text-light);
  }
  .contacts {
    position: absolute;
    right: 27px;
    top: 210px;
    list-style: none;
    text-align: right;
    font-family: "Open Sans", Arial, sans-serif;
    font-size: 12.5px;
    line-height: 18.5px;
    color: var(--text-light);
  }
  .contacts b { font-weight: 600; font-style: italic; }

  .front-mark {
    position: absolute;
    left: 0; right: 0;
    display: flex;
    align-items: center;
    justify-content: center;
    gap: 16px;
  }
  .card-front-1 .front-mark { top: 110px; }
  .front-mark-dot { width: 56px; height: 56px; border-radius: 50%; background: var(--accent); flex: none; }
  .front-mark-name { font-size: 40px; color: var(--accent); white-space: nowrap; }
  .card-front-2 .front-mark { top: 118px; }
  .card-front-2 .front-mark-dot { width: 46px; height: 46px; }
  .card-front-2 .front-mark-name { font-size: 35px; color: var(--text-light); }

  .site {
    position: absolute;
    left: 0; right: 0;
    top: 258px;
    text-align: center;
    font-size: 20px;
    letter-spacing: 3.5px;
    color: var(--text-light);
  }
</style>
</head>
<body>
  <p class="view-label label-back">Back</p>
  <section class="card card-back">
    <svg class="wave" viewBox="0 0 525 300" aria-hidden="true">
      <path d="M0,0 H525 V86 C450,92 380,92 300,72 C210,48 110,34 0,44 Z" fill="var(--band)"/>
      <path d="M0,44 C110,34 210,48 300,72 C380,92 450,92 525,86 V90 C450,98 380,100 300,84 C210,66 110,54 0,58 Z" fill="var(--stripe-dark)"/>
      <path d="M0,58 C110,54 210,66 300,84 C380,100 450,98 525,90 V94 C450,104 380,106 300,94 C210,80 110,72 0,78 Z" fill="var(--stripe-light)"/>
    </svg>
    <div class="holder">
      <p class="holder-name">Your Name</p>
      <p class="holder-role">Designation</p>
    </div>
    <p class="brand-name">The Kestrel Works</p>
    <p class="address">0000#, Area Name<br>State Name, Country code</p>
    <ul class="contacts">
      <li><b>c :</b> 123-456-7890</li>
      <li><b>p :</b> 123-456-7890</li>
      <li><b>e :</b> info@website.com</li>
      <li><b>w :</b> www.website.com</li>
    </ul>
  </section>

  <p class="view-label label-front-1">Front - 1</p>
  <section class="card card-front-1">
    <div class="front-mark">
      <span class="front-mark-dot"></span>
      <span class="front-mark-name">The Kestrel Works</span>
    </div>
    <p class="site">www.website.com</p>
  </section>

  <p class="view-label label-front-2">Front - 2</p>
  <section class="card card-front-2">
    <div class="front-mark">
      <span class="front-mark-dot"></span>
      <span class="front-mark-name">The Kestrel Works</span>
    </div>
    <p class="site">www.website.com</p>
  </section>
</body>
</html>
```